New Bicycle shop business card

Hi!
I'm looking for a business card for my new proffesional bike mechanics shop. This shop is only for fixing broken bikes and not selling bikes.
Peferbly a modern and sleek and modern design.
Colors: black, grey, red, white
Information:
Name: Rijwielwerkplaats Vanhoutte
Shop owner: Bart Vanhoutte & Marieke Segers
Website: www.rijwielwerkplaats-vanhoutte.be
Email: info@rijwielwerkplaats-vanhoutte.be
Phone number: +32471902368
Street adres: Kerkweg 46
9940 Bellebeke
Slogan/shop information: Herstellingen van alle merken.
Logo: see files.
Target Market(s)
People who seek a mechanic to fix or upgrade their bikes.
Contact Information for Business Card
Information:
Website: info@rijwielwerkplaats-vanhoutte.be
9940 Bellebeke
Logo: see files.

```html
<!DOCTYPE html>
<html lang="nl">
<head>
<meta charset="utf-8">
<title>Rijwielwerkplaats Vanhoutte – Visitekaartje</title>
<link rel="stylesheet" href="https://fonts.googleapis.com/css2?family=Montserrat:wght@700&family=Roboto:wght@400&display=swap">
<style>
  :root {
    --backdrop: #2e2e30;
    --card-black: #1f1f21;
    --card-dark: #262628;
    --brand-red: #dc3040;
    --stripe-grey: #a3a5a8;
    --text-white: #ffffff;
    --text-soft: #f1f1f1;
    --gloss: #5a5a5e;
  }
  * { box-sizing: border-box; margin: 0; padding: 0; }
  html, body { width: 799px; height: 1200px; overflow: hidden; }
  body {
    background: var(--backdrop);
    position: relative;
    font-family: "Roboto", Arial, sans-serif;
  }
  .card {
    position: absolute;
    left: 100px;
    width: 600px;
    height: 343px;
    border-radius: 22px;
    overflow: hidden;
    box-shadow: 0 10px 28px rgba(0,0,0,.45);
  }
  .card--front { top: 90px; background: var(--card-black); }
  .card--back  { top: 700px; background: var(--card-dark); }

  .front-mark {
    position: absolute; inset: 0;
    display: flex; flex-direction: column; align-items: center; justify-content: center; gap: 14px;
  }
  .front-mark__dot {
    width: 22px; height: 22px; border-radius: 50%;
    background: var(--gloss);
  }
  .front-mark__name {
    font-family: "Montserrat", Arial, sans-serif; font-weight: 700;
    font-size: 22px; letter-spacing: 2px; color: var(--gloss); text-transform: uppercase;
  }

  .back-art { position: absolute; inset: 0; }
  .brand {
    position: absolute; left: 34px; top: 24px;
    display: flex; align-items: center; gap: 12px;
  }
  .brand__square { width: 26px; height: 26px; background: var(--brand-red); }
  .brand__name {
    font-family: "Montserrat", Arial, sans-serif; font-weight: 700;
    font-size: 21px; letter-spacing: 1.5px; color: var(--text-white); text-transform: uppercase;
    line-height: 1.15;
  }
  .contact {
    position: absolute; left: 34px; top: 88px;
    list-style: none; color: var(--text-soft); font-size: 14px; line-height: 20px;
  }
  .contact li { display: flex; align-items: center; gap: 10px; white-space: nowrap; }
  .contact svg { width: 12px; height: 12px; fill: var(--brand-red); flex: none; }
  .person {
    position: absolute; right: 36px; bottom: 30px; text-align: right; color: var(--text-white);
  }
  .person__name {
    font-family: "Montserrat", Arial, sans-serif; font-weight: 700;
    font-size: 22px; letter-spacing: 1px; text-transform: uppercase;
  }
  .person__role { font-size: 14px; margin-top: 4px; }
</style>
</head>
<body>

  <section class="card card--front" aria-label="Voorkant visitekaartje">
    <div class="front-mark">
      <span class="front-mark__dot"></span>
      <span class="front-mark__name">Rijwielwerkplaats Vanhoutte</span>
    </div>
  </section>

  <section class="card card--back" aria-label="Achterkant visitekaartje">
    <svg class="back-art" viewBox="0 0 600 343" preserveAspectRatio="none" aria-hidden="true">
      <circle cx="470" cy="150" r="110" fill="#2c2c2f"/>
      <g transform="translate(0 20)">
        <path d="M0 195 C 90 160, 170 235, 300 250 C 420 262, 520 225, 600 238 L600 343 L0 343 Z" fill="var(--brand-red)"/>
        <path d="M0 168 C 100 150, 170 215, 300 228 C 420 240, 520 205, 600 218 L600 232 C 520 220, 420 252, 300 242 C 170 228, 100 170, 0 186 Z" fill="var(--stripe-grey)"/>
        <path d="M0 186 C 100 170, 170 228, 300 242 C 420 252, 520 220, 600 232 L600 240 C 520 228, 420 262, 300 252 C 170 238, 90 162, 0 197 Z" fill="var(--card-dark)"/>
      </g>
    </svg>

    <div class="brand">
      <span class="brand__square"></span>
      <span class="brand__name">Rijwielwerkplaats<br>Vanhoutte</span>
    </div>

    <ul class="contact">
      <li><svg viewBox="0 0 24 24"><path d="M6.6 10.8a15 15 0 0 0 6.6 6.6l2.2-2.2c.3-.3.7-.4 1-.2 1.1.4 2.3.6 3.6.6.6 0 1 .4 1 1V20c0 .6-.4 1-1 1A17 17 0 0 1 3 4c0-.6.4-1 1-1h3.5c.6 0 1 .4 1 1 0 1.3.2 2.5.6 3.6.1.3 0 .7-.2 1z"/></svg>+32471902368</li>
      <li><svg viewBox="0 0 24 24"><circle cx="12" cy="12" r="10"/></svg>www.rijwielwerkplaats-vanhoutte.be</li>
      <li><svg viewBox="0 0 24 24"><path d="M2 5h20v14H2z M2 5l10 8 10-8" stroke="#262628" stroke-width="1.5"/></svg>info@rijwielwerkplaats-vanhoutte.be</li>
      <li class="contact__address">Kerkweg 46 9940 Bellebeke</li>
    </ul>

    <div class="person">
      <div class="person__name">Marieke Segers</div>
      <div class="person__role">Owner</div>
    </div>
  </section>

</body>
</html>
```